Front cover for our tenth anniversary show programme

To create an eye catching tenth anniversary front cover for our programme

Moonbrook presents DANCE! 2015

date of the show Sunday 3rd May 2015

Venue The Harwick Playhouse

please see the updated brief!

Reason: there hasn't been anything that is quite right

```html
<!DOCTYPE html>
<html lang="en">
<head>
<meta charset="utf-8">
<title>Moonbrook presents DANCE! 2015 – Programme Cover</title>
<link rel="stylesheet" href="https://fonts.googleapis.com/css2?family=Anton&family=Oswald:wght@500;700&display=swap">
<style>
  :root {
    --backdrop: #e4e5e7;
    --ink: #111113;
    --white: #ffffff;
    --pink: #e8318f;
    --stage-blue: #2c3fa8;
    --stage-purple: #6b2d8c;
    --stage-magenta: #a8235f;
    --stage-red: #b3202e;
    --stage-orange: #d26a2a;
    --stage-dark: #221828;
  }
  * { box-sizing: border-box; margin: 0; padding: 0; }
  html, body { width: 1200px; height: 850px; overflow: hidden; }
  body {
    background: var(--backdrop);
    font-family: "Oswald", "Arial Narrow", sans-serif;
    position: relative;
  }
  .programme-cover {
    position: absolute;
    left: 350px; top: 45px;
    width: 500px; height: 760px;
    overflow: hidden;
    background: var(--stage-dark);
  }
  .photo-collage { position: absolute; inset: 0; }
  .collage-tile { position: absolute; }
  .tile-stage-blue   { left: 0; top: 0; width: 160px; height: 150px; background: linear-gradient(135deg, #3a4fd0, #1a2170 70%, #0d1240); }
  .tile-stage-top    { left: 160px; top: 0; width: 190px; height: 150px; background: linear-gradient(160deg, #7a3f7e, #3b2240); }
  .tile-stage-right  { left: 350px; top: 0; width: 150px; height: 150px; background: linear-gradient(200deg, #5c6a3a, #2a2430); }
  .tile-red-fans     { left: 0; top: 150px; width: 150px; height: 140px; background: linear-gradient(150deg, #c2304a, #6e1020); }
  .tile-pink-mid     { left: 150px; top: 150px; width: 120px; height: 190px; background: linear-gradient(180deg, #a8235f, #5a1240); }
  .tile-magenta-right{ left: 270px; top: 150px; width: 230px; height: 260px; background: linear-gradient(200deg, #d14a98, #7a2a8c 60%, #3d1850); }
  .tile-solo-purple  { left: 0; top: 290px; width: 150px; height: 200px; background: linear-gradient(180deg, #5e3aa8, #8a3d8f 60%, #c04a6a); }
  .tile-dark-centre  { left: 150px; top: 340px; width: 160px; height: 170px; background: linear-gradient(160deg, #3b2b4a, #1a1520); }
  .tile-rose-group   { left: 310px; top: 410px; width: 190px; height: 140px; background: linear-gradient(170deg, #b0406e, #5e1e3a); }
  .tile-lilac-low    { left: 200px; top: 510px; width: 150px; height: 250px; background: linear-gradient(180deg, #7d6a9c, #b89ac0 50%, #5a4670); }
  .tile-orange-solo  { left: 350px; top: 550px; width: 150px; height: 210px; background: linear-gradient(160deg, #6a2a20, #d26a2a 55%, #3a1a18); }
  .tile-violet-left  { left: 0; top: 490px; width: 200px; height: 270px; background: linear-gradient(180deg, #6a4aa0, #3a2a60); }

  .star-panel { position: absolute; inset: 0; width: 500px; height: 760px; }

  .show-heading {
    position: absolute;
    right: 28px; top: 98px;
    text-align: right;
    color: var(--white);
    text-transform: uppercase;
  }
  .show-presenter {
    font-family: "Oswald", "Arial Narrow", sans-serif;
    font-weight: 700;
    font-size: 25px;
    line-height: 1;
    letter-spacing: 0.2px;
  }
  .show-title {
    font-family: "Anton", "Impact", sans-serif;
    font-size: 148px;
    line-height: 0.98;
    letter-spacing: -1px;
  }
  .show-details {
    position: absolute;
    left: 240px; top: 428px;
    color: var(--white);
    font-weight: 700;
    font-size: 16.5px;
    line-height: 1.32;
    text-transform: uppercase;
  }
  .company-mark {
    position: absolute;
    left: 48px; top: 624px;
    width: 220px;
    text-align: center;
    color: var(--white);
  }
  .company-name {
    display: flex; align-items: center; justify-content: center; gap: 8px;
    font-weight: 500;
    font-size: 34px;
    line-height: 1;
  }
  .company-name::before {
    content: "";
    width: 14px; height: 14px;
    border-radius: 50%;
    background: var(--white);
  }
  .anniversary-line {
    margin-top: 6px;
    font-weight: 500;
    font-size: 17px;
    line-height: 1.1;
  }
  .anniversary-years {
    color: var(--pink);
    font-weight: 700;
    font-size: 26px;
    line-height: 1;
  }
</style>
</head>
<body>
  <main class="programme-cover">
    <div class="photo-collage" role="img" aria-label="Collage of stage photographs of young dancers performing in colourful costumes under stage lights">
      <div class="collage-tile tile-stage-blue"></div>
      <div class="collage-tile tile-stage-top"></div>
      <div class="collage-tile tile-stage-right"></div>
      <div class="collage-tile tile-red-fans"></div>
      <div class="collage-tile tile-pink-mid"></div>
      <div class="collage-tile tile-magenta-right"></div>
      <div class="collage-tile tile-solo-purple"></div>
      <div class="collage-tile tile-dark-centre"></div>
      <div class="collage-tile tile-rose-group"></div>
      <div class="collage-tile tile-lilac-low"></div>
      <div class="collage-tile tile-orange-solo"></div>
      <div class="collage-tile tile-violet-left"></div>
    </div>

    <svg class="star-panel" viewBox="0 0 500 760" aria-hidden="true">
      <polygon points="160,330 226.4,508.6 416.8,516.6 267.5,634.9 318.7,818.4 160,713 1.3,818.4 52.5,634.9 -96.8,516.6 93.6,508.6"
               fill="#111113" stroke="#ffffff" stroke-width="7" stroke-linejoin="miter"/>
    </svg>

    <header class="show-heading">
      <p class="show-presenter">Moonbrook presents</p>
      <h1 class="show-title">DANCE<br>2015</h1>
    </header>

    <p class="show-details">
      Date of the show<br>
      Sunday 3rd May 2015<br>
      Venue The Harwick Playhouse
    </p>

    <div class="company-mark">
      <p class="company-name">Moonbrook</p>
      <p class="anniversary-line">Celebrating</p>
      <p class="anniversary-years">Ten Years</p>
    </div>
  </main>
</body>
</html>
```